Brivolt Technologies business card design

We need a business card designed with our new logo. it would be great if the card could communicate it is a technology based company.

Target Market(s)

system integrators

Industry/Entity Type

technology, IOT

Contact Information for Business Card

Name, designation, Address, telephone number, email address

Requirements
Must have
• logo and company name
Nice to have
• something to do with technology

```html
<!DOCTYPE html>
<html lang="en">
<head>
<meta charset="utf-8">
<title>Brivolt Technologies business card</title>
<link rel="stylesheet" href="https://fonts.googleapis.com/css2?family=Exo+2:ital,wght@0,700;0,800;1,800&family=Open+Sans:ital,wght@0,400;1,400&display=swap">
<style>
  :root {
    --stage: #e6e6e4;
    --card: #1a1a1a;
    --card-deep: #0c0c0c;
    --relief: #3a3a3a;
    --accent: #f7941d;
    --ink: #f2f2f2;
    --ink-soft: #d9d9d9;
  }
  * { box-sizing: border-box; margin: 0; padding: 0; }
  html, body { width: 1200px; height: 900px; overflow: hidden; }
  body {
    background: var(--stage);
    font-family: "Open Sans", sans-serif;
    display: flex;
    flex-direction: column;
    align-items: center;
    justify-content: center;
    gap: 36px;
  }
  .card {
    position: relative;
    width: 700px;
    height: 400px;
    background: var(--card);
    border-bottom: 2px solid var(--accent);
    overflow: hidden;
    box-shadow: 0 10px 26px rgba(0,0,0,.25);
  }
  .wordmark {
    display: flex;
    align-items: center;
    gap: 12px;
    font-family: "Exo 2", sans-serif;
    font-weight: 800;
    text-transform: uppercase;
    color: var(--ink);
    line-height: 1;
  }
  .wordmark-square {
    width: 14px; height: 14px;
    background: var(--accent);
    flex: none;
  }
  /* front */
  .card-front .wordmark {
    position: absolute;
    left: 52px; top: 48px;
    font-size: 30px;
    letter-spacing: 1px;
  }
  .address {
    position: absolute;
    left: 52px; top: 128px;
    color: var(--ink-soft);
    font-size: 15px;
    line-height: 1.5;
  }
  .contacts {
    position: absolute;
    left: 52px; top: 196px;
    list-style: none;
    color: var(--ink-soft);
    font-size: 15px;
    line-height: 1.7;
  }
  .contacts li { display: flex; align-items: center; gap: 10px; }
  .contacts svg { width: 14px; height: 14px; flex: none; }
  .person {
    position: absolute;
    right: 52px; top: 150px;
    text-align: right;
  }
  .person-name {
    font-family: "Exo 2", sans-serif;
    font-weight: 800;
    font-style: italic;
    font-size: 24px;
    color: var(--accent);
    text-transform: uppercase;
    letter-spacing: .5px;
  }
  .person-title {
    font-style: italic;
    color: var(--ink-soft);
    font-size: 15px;
    margin-top: 4px;
  }
  .front-decor {
    position: absolute;
    right: 0; bottom: 0;
    width: 360px; height: 150px;
    background: linear-gradient(120deg, var(--card) 0%, var(--card-deep) 45%, var(--relief) 100%);
    clip-path: polygon(30% 0, 100% 0, 100% 100%, 0 100%);
    opacity: .9;
  }
  /* back */
  .back-decor {
    position: absolute;
    left: 70px; top: 0;
    width: 430px; height: 250px;
    background: linear-gradient(135deg, var(--card-deep) 0%, var(--card) 40%, var(--relief) 100%);
    clip-path: polygon(12% 0, 100% 0, 88% 100%, 0 100%);
  }
  .card-back .wordmark {
    position: absolute;
    right: 52px; bottom: 56px;
    font-size: 40px;
    letter-spacing: 1px;
  }
</style>
</head>
<body>
  <section class="card card-front" aria-label="Card front">
    <div class="wordmark"><span class="wordmark-square"></span>Brivolt Technologies</div>
    <p class="address">1870 Harbor Crest Dr<br>Seacliff CA 92701</p>
    <ul class="contacts">
      <li>
        <svg viewBox="0 0 16 16" aria-hidden="true"><path fill="var(--accent)" d="M4 1l3 3-2 2c1 2 3 4 5 5l2-2 3 3-2 2C7 14 2 9 2 3z"/></svg>
        555-310-4827
      </li>
      <li>
        <svg viewBox="0 0 16 16" aria-hidden="true"><rect x="1" y="3" width="14" height="10" fill="var(--accent)"/><path d="M1 3l7 6 7-6" fill="none" stroke="var(--card)" stroke-width="1.5"/></svg>
        info@brivolttech.com
      </li>
      <li>
        <svg viewBox="0 0 16 16" aria-hidden="true"><circle cx="8" cy="8" r="6.5" fill="none" stroke="var(--accent)" stroke-width="1.5"/><path d="M1.5 8h13M8 1.5c-3 3-3 10 0 13M8 1.5c3 3 3 10 0 13" fill="none" stroke="var(--accent)" stroke-width="1.2"/></svg>
        www.brivolttech.com
      </li>
    </ul>
    <div class="person">
      <p class="person-name">Dario Kellen</p>
      <p class="person-title">President</p>
    </div>
    <div class="front-decor" role="img" aria-label="Large embossed brand symbol in dark relief"></div>
  </section>

  <section class="card card-back" aria-label="Card back">
    <div class="back-decor" role="img" aria-label="Large embossed brand symbol in dark grey relief"></div>
    <div class="wordmark"><span class="wordmark-square"></span>Brivolt Technologies</div>
  </section>
</body>
</html>
```